Easy Marinade Labels for Butchery Store

Need a set of labels designed for a Butchery Shop. They will sit in the top left corner of the packets as a triangle (7cm each side). Easy because the only major requirement is the label name and some small text saying "Please ask in store to see spec sheet for ingredients". Extra points for finding a fun way to incorporate the logo and/or images of food (garlic bulbs, chilli, spices ect) to enhance the label. List of Marinade Names below: GarlicPepper Mint & RosemarySatayBBQChilli Plum & GingerSundried Tomato & BasilBuffaloHoney SoyHoi-SinPer PeriSpicy CajunTeriyakiBlack Bean Ive also attached the logo and an example of how the label might sit on a packet of meat. Thanks

Target Market(s)

Butchery Deli Shop Customers

Industry/Entity Type

Food Store

Font styles to use
Serif
Sans Serif
Decorative
Other font styles liked:
• Fun font that isn't a generic Quellbrix Font?

Colors

Designer to choose colors to be used in the design.

Requirements
Must have
• Product Name
• Small text saying "Please ask in store to see spec sheet for ingredients"
Nice to have
• Photos of ingredients that would match that type of marinade - Chilli, Garlic, Spices.
• Fenly Oak Logo - not essential if it doesn't look good on the label / doesn't fit.

```html
<!DOCTYPE html>
<html lang="en">
<head>
<meta charset="utf-8">
<title>Teriyaki Sauce Marinade Label</title>
<link href="https://fonts.googleapis.com/css2?family=Permanent+Marker&family=League+Spartan:wght@700;800&display=swap" rel="stylesheet">
<style>
  :root {
    --canvas: #ffffff;
    --frame-yellow: #f2e81c;
    --leaf-deep: #2f5a1c;
    --leaf-mid: #5f9a2e;
    --leaf-light: #9bc23f;
    --ginger-tan: #c9a77f;
    --honey: #a8641c;
    --label-text: #ffffff;
    --text-edge: #1d2a12;
  }
  html, body {
    margin: 0;
    padding: 0;
    width: 1200px;
    height: 900px;
    overflow: hidden;
    background: var(--canvas);
  }
  .label-sheet {
    display: block;
    width: 1200px;
    height: 900px;
  }
  .label-kicker {
    font-family: "League Spartan", Arial, sans-serif;
    font-weight: 800;
    font-size: 14px;
    fill: var(--label-text);
    stroke: var(--text-edge);
    stroke-width: 1.5px;
    paint-order: stroke;
  }
  .label-name {
    font-family: "Permanent Marker", "Comic Sans MS", cursive;
    font-size: 74px;
    fill: var(--label-text);
    stroke: var(--text-edge);
    stroke-width: 2px;
    paint-order: stroke;
  }
  .label-notice {
    font-family: "League Spartan", Arial, sans-serif;
    font-weight: 800;
    font-size: 23px;
    fill: var(--label-text);
    stroke: var(--text-edge);
    stroke-width: 3px;
    paint-order: stroke;
  }
</style>
</head>
<body>
<svg class="label-sheet" viewBox="0 0 1200 900" xmlns="http://www.w3.org/2000/svg">
  <defs>
    <linearGradient id="ingredient-tones" x1="0" y1="0" x2="0.25" y2="1">
      <stop offset="0" stop-color="var(--honey)"/>
      <stop offset="0.22" stop-color="var(--ginger-tan)"/>
      <stop offset="0.45" stop-color="var(--leaf-light)"/>
      <stop offset="0.75" stop-color="var(--leaf-mid)"/>
      <stop offset="1" stop-color="var(--leaf-deep)"/>
    </linearGradient>
  </defs>

  <g class="marinade-label">
    <polygon class="label-frame" points="623,170 1104,651 142,651" fill="var(--frame-yellow)"/>
    <polygon class="label-artwork" role="img"
      aria-label="Watercolour illustration of fresh ginger root, green leaves and honey dippers dripping honey over a bed of green herbs"
      points="623,181 1089,645 157,645" fill="url(#ingredient-tones)"/>

    <text class="label-kicker" x="623" y="394" text-anchor="middle" textLength="170" lengthAdjust="spacing">MARINATED WITH</text>
    <text class="label-name" x="627" y="494" text-anchor="middle" textLength="218" lengthAdjust="spacingAndGlyphs">TERIYAKI</text>
    <text class="label-name" x="624" y="576" text-anchor="middle" textLength="185" lengthAdjust="spacingAndGlyphs">SAUCE</text>
    <text class="label-notice" x="624" y="623" text-anchor="middle" textLength="745" lengthAdjust="spacingAndGlyphs">PLEASE ASK IN STORE TO SEE SPEC SHEET FOR INGREDIENTS</text>
  </g>
</svg>
</body>
</html>
```